BRIGHTHOLD PROPERTY MANAGEMENT INC. WEBSITE

Please make the website more family-friendly.

I want a website to help me build my property management business by adding listing properties and creating an online application. Im open to any other ideas.
I want a WordPress designer to code it.

Here is my current website. www.brighthold.biz

IDEA: I like the website design https://www.pelicanclimateservices.com/

Thank you

Tom

Number of Pages Required

5+ page

```html
<!DOCTYPE html>
<html lang="en">
<head>
<meta charset="UTF-8">
<title>Brighthold Property Management</title>
<link href="https://fonts.googleapis.com/css2?family=Poppins:wght@400;500;600&display=swap" rel="stylesheet">
<style>
:root{
  --brand:#a00f14;
  --brand-deep:#9a0d13;
  --ink:#111;
  --muted:#555;
  --line:#e6e6e6;
  --white:#fff;
  --green:#0fd10f;
  --red-tag:#f01f1f;
}
*{box-sizing:border-box;margin:0;padding:0}
html,body{width:1200px;height:2649px;overflow:hidden}
body{font-family:"Poppins",sans-serif;color:var(--ink);background:var(--white);position:relative}
a{color:inherit;text-decoration:none}

/* header */
.site-header{height:73px;display:flex;align-items:center;padding:0 67px;justify-content:space-between}
.brand{display:flex;align-items:center;gap:8px;color:var(--brand);font-weight:600;font-size:17px;letter-spacing:.5px}
.brand-mark{width:22px;height:22px;border-radius:50%;background:var(--brand)}
.main-nav{display:flex;gap:20px;font-size:14px;color:#222}
.main-nav span{display:flex;align-items:center;gap:8px}
.chev{width:10px;height:10px}

/* hero */
.hero{height:500px;position:relative;display:flex;flex-direction:column;align-items:center;
  background:linear-gradient(180deg,#5f86a8 0%,#8aa0a0 40%,#3d5a2c 75%,#2a4020 100%)}
.hero-title{color:var(--white);font-size:54px;font-weight:600;line-height:74px;text-align:center;margin-top:105px;text-shadow:0 2px 8px rgba(0,0,0,.3)}
.hero-sub{color:var(--white);font-size:16px;margin-top:8px;text-shadow:0 1px 4px rgba(0,0,0,.4)}
.search-bar{margin-top:12px;width:562px;height:64px;border-radius:10px;background:rgba(255,255,255,.35);display:flex;align-items:center;justify-content:space-between;padding:0 10px 0 17px}
.search-bar span{color:var(--white);font-size:15px}
.btn{background:var(--brand);color:var(--white);border-radius:8px;font-size:15px;display:flex;align-items:center;justify-content:center}
.search-bar .btn{width:102px;height:44px}

/* explore */
.section-title{font-size:35px;font-weight:500;text-align:center}
.explore .section-title{margin-top:48px}
.explore-grid{position:relative;height:267px;margin-top:28px;overflow:hidden}
.tile{position:absolute;border-radius:14px;overflow:hidden}
.tile.tall{height:267px;width:222px;top:0}
.tile.half{height:123px;width:222px}
.ph-building{background:linear-gradient(160deg,#6fa0c4,#d8dde0 55%,#9ea89a)}
.ph-dusk{background:linear-gradient(180deg,#a58ac4,#c9a9b9 45%,#4a5a4a 75%,#2f4a2a)}
.ph-city{background:linear-gradient(180deg,#7fa6cf,#bcc4c2 45%,#c8a650 65%,#3d5a2c)}
.ph-house{background:linear-gradient(180deg,#4d8fd0,#b8a793 50%,#7a8a5a)}
.tag{position:absolute;left:16px;bottom:16px;background:var(--white);border-radius:6px;height:30px;padding:0 14px;display:flex;align-items:center;gap:14px;font-size:12px;color:var(--brand)}
.tag svg{width:10px;height:10px}

/* listings */
.listings .section-title{margin-top:60px}
.listing-row{display:flex;gap:26px;padding:0 67px;margin-top:36px}
.listing-card{width:247px;height:355px;border-radius:14px;box-shadow:0 4px 18px rgba(0,0,0,.08);overflow:hidden;background:var(--white)}
.listing-photo{height:200px;position:relative}
.ph-lawn1{background:linear-gradient(180deg,#8fb0c8,#a38a6c 50%,#5e8c3a)}
.ph-lawn2{background:linear-gradient(180deg,#4a86c8,#d5d8dc 50%,#3fa032)}
.ph-lawn3{background:linear-gradient(180deg,#5b9ad6,#cbb89a 50%,#4e9a30)}
.ph-lawn4{background:linear-gradient(180deg,#5b8fc8,#c9a07a 55%,#7da040)}
.badge{position:absolute;bottom:16px;height:30px;border-radius:6px;font-size:12px;display:flex;align-items:center;padding:0 14px}
.badge.status{left:16px;color:#111;background:var(--green)}
.badge.status.rented{background:var(--red-tag);color:var(--white)}
.badge.kind{right:16px;background:var(--white)}
.listing-body{padding:14px 16px}
.price{font-size:24px;font-weight:500}
.specs{display:flex;gap:18px;margin-top:8px;font-size:14px}
.specs span{display:flex;align-items:center;gap:8px}
.specs svg{width:18px;height:14px}
.addr{margin-top:16px;font-size:13.5px;color:var(--muted);line-height:20px}

/* services */
.services{position:absolute;top:1529px;left:0;width:1200px;height:757px;
  background:linear-gradient(135deg,#a3454f,#b54a4f 40%,#b8433a 70%,#8f3a2c)}
.services .section-title{color:var(--white);position:absolute;top:64px;width:100%;font-size:36px}
.ring{position:absolute;left:397px;top:157px;width:406px;height:406px;border-radius:50%;background:var(--white)}
.ring-photo{position:absolute;left:49px;top:49px;width:308px;height:308px;border-radius:50%;background:radial-gradient(circle at 50% 45%,#e8d64a,#7cbc3a 55%,#3f8a2a)}
.dot{position:absolute;width:11px;height:11px;border-radius:50%;background:var(--brand-deep);transform:translate(-50%,-50%)}
.svc{position:absolute;display:flex;align-items:center;gap:18px;color:var(--white);font-size:14px;line-height:20px}
.svc.left{flex-direction:row-reverse;text-align:right;transform:translate(-100%,-50%)}
.svc.right{transform:translate(0,-50%)}
.svc-icon{width:50px;height:50px;border-radius:50%;background:var(--white);border:3px solid rgba(255,255,255,.55);box-shadow:0 0 0 3px rgba(160,15,20,.35);display:flex;align-items:center;justify-content:center;flex:none}
.svc-icon svg{width:20px;height:20px}
.svc.bottom{flex-direction:column;gap:8px;text-align:center;transform:translate(-50%,-25px)}

/* footer */
.site-footer{position:absolute;top:2286px;left:0;width:1200px;height:363px;background:var(--brand-deep);color:var(--white)}
.footer-brand{position:absolute;left:67px;top:55px;width:184px;height:52px;background:var(--white);border-radius:8px;display:flex;align-items:center;justify-content:center}
.socials{position:absolute;left:67px;top:122px;display:flex;gap:20px}
.socials span{width:20px;height:20px;border:2px solid var(--white);border-radius:50%}
.f-col{position:absolute;top:64px}
.f-col h4{font-size:17px;font-weight:500;margin-bottom:14px}
.f-col li{list-style:none;font-size:13.5px;line-height:29px}
.newsletter{position:absolute;left:733px;top:91px;width:400px;height:64px;border-radius:10px;background:rgba(255,255,255,.3);display:flex;align-items:center;justify-content:space-between;padding:0 10px 0 17px}
.newsletter span{font-size:15px}
.newsletter .btn{width:124px;height:44px}
.f-rule{position:absolute;left:67px;right:67px;top:276px;border-top:1px solid rgba(255,255,255,.3)}
.copy{position:absolute;left:67px;top:302px;font-size:13.5px}
</style>
</head>
<body>

<header class="site-header">
  <div class="brand"><span class="brand-mark"></span>BRIGHTHOLD</div>
  <nav class="main-nav">
    <span>Listing</span>
    <span>Owners <svg class="chev" viewBox="0 0 10 10"><path d="M1 3l4 4 4-4" fill="none" stroke="#222" stroke-width="1.3"/></svg></span>
    <span>Prospect Tenants <svg class="chev" viewBox="0 0 10 10"><path d="M1 3l4 4 4-4" fill="none" stroke="#222" stroke-width="1.3"/></svg></span>
    <span>About</span>
    <span>Contact</span>
    <span>Community</span>
    <span>Mortgage Info <svg class="chev" viewBox="0 0 10 10"><path d="M1 3l4 4 4-4" fill="none" stroke="#222" stroke-width="1.3"/></svg></span>
  </nav>
</header>

<section class="hero" role="img" aria-label="City riverfront skyline with a tiered golden building and trees">
  <h1 class="hero-title">Discover a place<br>you'll love to live</h1>
  <p class="hero-sub">Search millions of apartments and houses with Brighthold</p>
  <div class="search-bar"><span>Enter an Address, Neighborhood, City, or ZIP Code</span><a class="btn">Search</a></div>
</section>

<section class="explore">
  <h2 class="section-title">Explore homes on Brighthold</h2>
  <div class="explore-grid">
    <div class="tile tall ph-building" style="left:67px" role="img" aria-label="White apartment building with palm trees">
      <span class="tag">Sacramento <svg viewBox="0 0 10 10"><path d="M2 8L8 2M3 2h5v5" fill="none" stroke="#a00f14" stroke-width="1.2"/></svg></span></div>
    <div class="tile half ph-dusk" style="left:309px;top:0" role="img" aria-label="Modern house at dusk">
      <span class="tag">Antelope <svg viewBox="0 0 10 10"><path d="M2 8L8 2M3 2h5v5" fill="none" stroke="#a00f14" stroke-width="1.2"/></svg></span></div>
    <div class="tile half ph-city" style="left:309px;top:144px" role="img" aria-label="City skyline by the river">
      <span class="tag">Carmichael <svg viewBox="0 0 10 10"><path d="M2 8L8 2M3 2h5v5" fill="none" stroke="#a00f14" stroke-width="1.2"/></svg></span></div>
    <div class="tile tall ph-house" style="left:551px" role="img" aria-label="Two-storey suburban homes">
      <span class="tag">Citrus Heights <svg viewBox="0 0 10 10"><path d="M2 8L8 2M3 2h5v5" fill="none" stroke="#a00f14" stroke-width="1.2"/></svg></span></div>
    <div class="tile half ph-dusk" style="left:793px;top:0" role="img" aria-label="Modern house at dusk">
      <span class="tag">El Dorado County <svg viewBox="0 0 10 10"><path d="M2 8L8 2M3 2h5v5" fill="none" stroke="#a00f14" stroke-width="1.2"/></svg></span></div>
    <div class="tile half ph-city" style="left:793px;top:144px" role="img" aria-label="City skyline by the river">
      <span class="tag">El Dorado Hills <svg viewBox="0 0 10 10"><path d="M2 8L8 2M3 2h5v5" fill="none" stroke="#a00f14" stroke-width="1.2"/></svg></span></div>
    <div class="tile tall ph-building" style="left:1035px" role="img" aria-label="White apartment building with palm trees">
      <span class="tag">Elverta <svg viewBox="0 0 10 10"><path d="M2 8L8 2M3 2h5v5" fill="none" stroke="#a00f14" stroke-width="1.2"/></svg></span></div>
  </div>
</section>

<section class="listings">
  <h2 class="section-title">Newly listed homes in Sacramento</h2>
  <div class="listing-row">
    <article class="listing-card">
      <div class="listing-photo ph-lawn1" role="img" aria-label="Stone craftsman house with lawn"><span class="badge status">Available</span><span class="badge kind">Residential</span></div>
      <div class="listing-body">
        <div class="price">$2,000</div>
        <div class="specs">
          <span><svg viewBox="0 0 18 14"><path d="M1 2v11M1 9h16v4M4 6h4v3M8 6h7a2 2 0 012 2v1" fill="none" stroke="#a00f14" stroke-width="1.3"/></svg>2</span>
          <span><svg viewBox="0 0 18 14"><path d="M2 7h14v3a3 3 0 01-3 3H5a3 3 0 01-3-3zM4 7V2a1 1 0 012 0" fill="none" stroke="#a00f14" stroke-width="1.3"/></svg>2</span>
          <span><svg viewBox="0 0 18 14"><path d="M2 1h14v6H9v6H2zM9 1v4M2 7h4" fill="none" stroke="#a00f14" stroke-width="1.3"/></svg>2</span>
        </div>
        <p class="addr">418 Linden Row<br>Fairview, CA 95012</p>
      </div>
    </article>
    <article class="listing-card">
      <div class="listing-photo ph-lawn2" role="img" aria-label="White gabled house with green lawn"><span class="badge status">Available</span><span class="badge kind">Residential</span></div>
      <div class="listing-body">
        <div class="price">$2,000</div>
        <div class="specs">
          <span><svg viewBox="0 0 18 14"><path d="M1 2v11M1 9h16v4M4 6h4v3M8 6h7a2 2 0 012 2v1" fill="none" stroke="#a00f14" stroke-width="1.3"/></svg>2</span>
          <span><svg viewBox="0 0 18 14"><path d="M2 7h14v3a3 3 0 01-3 3H5a3 3 0 01-3-3zM4 7V2a1 1 0 012 0" fill="none" stroke="#a00f14" stroke-width="1.3"/></svg>2</span>
          <span><svg viewBox="0 0 18 14"><path d="M2 1h14v6H9v6H2zM9 1v4M2 7h4" fill="none" stroke="#a00f14" stroke-width="1.3"/></svg>2</span>
        </div>
        <p class="addr">418 Linden Row<br>Fairview, CA 95012</p>
      </div>
    </article>
    <article class="listing-card">
      <div class="listing-photo ph-lawn3" role="img" aria-label="Single-storey stucco home with lawn"><span class="badge status rented">Rented</span><span class="badge kind">Residential</span></div>
      <div class="listing-body">
        <div class="price">$2,000</div>
        <div class="specs">
          <span><svg viewBox="0 0 18 14"><path d="M1 2v11M1 9h16v4M4 6h4v3M8 6h7a2 2 0 012 2v1" fill="none" stroke="#a00f14" stroke-width="1.3"/></svg>2</span>
          <span><svg viewBox="0 0 18 14"><path d="M2 7h14v3a3 3 0 01-3 3H5a3 3 0 01-3-3zM4 7V2a1 1 0 012 0" fill="none" stroke="#a00f14" stroke-width="1.3"/></svg>2</span>
          <span><svg viewBox="0 0 18 14"><path d="M2 1h14v6H9v6H2zM9 1v4M2 7h4" fill="none" stroke="#a00f14" stroke-width="1.3"/></svg>2</span>
        </div>
        <p class="addr">418 Linden Row<br>Fairview, CA 95012</p>
      </div>
    </article>
    <article class="listing-card">
      <div class="listing-photo ph-lawn4" role="img" aria-label="Ranch house with porch and garage"><span class="badge status">Available</span><span class="badge kind">Residential</span></div>
      <div class="listing-body">
        <div class="price">$2,000</div>
        <div class="specs">
          <span><svg viewBox="0 0 18 14"><path d="M1 2v11M1 9h16v4M4 6h4v3M8 6h7a2 2 0 012 2v1" fill="none" stroke="#a00f14" stroke-width="1.3"/></svg>2</span>
          <span><svg viewBox="0 0 18 14"><path d="M2 7h14v3a3 3 0 01-3 3H5a3 3 0 01-3-3zM4 7V2a1 1 0 012 0" fill="none" stroke="#a00f14" stroke-width="1.3"/></svg>2</span>
          <span><svg viewBox="0 0 18 14"><path d="M2 1h14v6H9v6H2zM9 1v4M2 7h4" fill="none" stroke="#a00f14" stroke-width="1.3"/></svg>2</span>
        </div>
        <p class="addr">418 Linden Row<br>Fairview, CA 95012</p>
      </div>
    </article>
  </div>
</section>

<section class="services" role="img" aria-label="Row of suburban townhouses under a red tint">
  <h2 class="section-title">Property Management Services</h2>
  <div class="ring"><div class="ring-photo" role="img" aria-label="Small yellow model house with a for rent tag on grass"></div></div>
  <span class="dot" style="left:440px;top:232px"></span>
  <span class="dot" style="left:759px;top:232px"></span>
  <span class="dot" style="left:393px;top:356px"></span>
  <span class="dot" style="left:806px;top:360px"></span>
  <span class="dot" style="left:431px;top:478px"></span>
  <span class="dot" style="left:765px;top:478px"></span>
  <span class="dot" style="left:593px;top:563px"></span>

  <div class="svc left" style="left:417px;top:208px"><span class="svc-icon"><svg viewBox="0 0 20 20"><path d="M2 2v16h16M5 15v-5M9 15V7M13 15v-4M5 10l4-3 4 4 4-5" fill="none" stroke="#a00f14" stroke-width="1.3"/></svg></span><span>Accounting<br>Service</span></div>
  <div class="svc right" style="left:793px;top:214px"><span class="svc-icon"><svg viewBox="0 0 20 20"><path d="M2 2v16h16M5 15v-5M9 15V7M13 15v-4M5 10l4-3 4 4 4-5" fill="none" stroke="#a00f14" stroke-width="1.3"/></svg></span><span>Leasing</span></div>
  <div class="svc left" style="left:376px;top:355px"><span class="svc-icon"><svg viewBox="0 0 20 20"><path d="M2 2v16h16M5 15v-5M9 15V7M13 15v-4M5 10l4-3 4 4 4-5" fill="none" stroke="#a00f14" stroke-width="1.3"/></svg></span><span>Mortgage<br>Utility Payments</span></div>
  <div class="svc right" style="left:836px;top:360px"><span class="svc-icon"><svg viewBox="0 0 20 20"><path d="M2 2v16h16M5 15v-5M9 15V7M13 15v-4M5 10l4-3 4 4 4-5" fill="none" stroke="#a00f14" stroke-width="1.3"/></svg></span><span>Security<br>Deposite</span></div>
  <div class="svc left" style="left:397px;top:508px"><span class="svc-icon"><svg viewBox="0 0 20 20"><path d="M2 2v16h16M5 15v-5M9 15V7M13 15v-4M5 10l4-3 4 4 4-5" fill="none" stroke="#a00f14" stroke-width="1.3"/></svg></span><span>Rent<br>Collection</span></div>
  <div class="svc right" style="left:799px;top:508px"><span class="svc-icon"><svg viewBox="0 0 20 20"><path d="M2 2v16h16M5 15v-5M9 15V7M13 15v-4M5 10l4-3 4 4 4-5" fill="none" stroke="#a00f14" stroke-width="1.3"/></svg></span><span>Inspections of<br>Property</span></div>
  <div class="svc bottom" style="left:593px;top:615px"><span class="svc-icon"><svg viewBox="0 0 20 20"><path d="M2 2v16h16M5 15v-5M9 15V7M13 15v-4M5 10l4-3 4 4 4-5" fill="none" stroke="#a00f14" stroke-width="1.3"/></svg></span><span>Repair &amp; Maintenance<br>Service</span></div>
</section>

<footer class="site-footer">
  <div class="footer-brand"><div class="brand"><span class="brand-mark"></span>BRIGHTHOLD</div></div>
  <div class="socials"><span></span><span></span><span></span><span></span></div>
  <div class="f-col" style="left:470px"><h4>Links</h4><ul><li>Listings</li><li>Owners</li><li>Prospect Tenants</li><li>About</li><li>Contact</li></ul></div>
  <div class="f-col" style="left:612px"><h4>Resource</h4><ul><li>Community</li><li>Mortgage Info</li></ul></div>
  <div class="f-col" style="left:733px"><h4>Subscribe to Our Newsletter</h4></div>
  <div class="newsletter"><span>Your Domain (example.com)</span><a class="btn">Subscribe</a></div>
  <div class="f-rule"></div>
  <p class="copy">© 2024 Brighthold. All rights reserved.</p>
</footer>

</body>
</html>
```